Agrarhandel benötigt Homepage
Zielgruppe
Wir sind ein Agrarhandel mit einem Warenumschlagslager im Sinne eines klassischen Einzelhandels und vertreiben Produkte an Landwirte.
Wir vertreiben folgende Hauptproduktgruppen:
Einzelfuttermittel
wie z.B. Sojaexktraktionsschrot. Die einzelnen Produkte könnten z.B. wie die Futtermittel auf folgender Seite dargestellt werden (https://www.kornprobe-beispiel.eu/de/produkt/trelomixan)
Mischfuttermittel
Hier bieten wir unseren Kunden an, individuelles Mischfutter auf Basis unserer Einzelfuttermittel herzustellen.
Weitere Details und weitere Produktbereiche habe ich in einer Powerpoint-Übersicht dargestellt.
Neben diesen Produkten wollen wir uns als Familienunternehmen selbst vorstellen. Zudem betreiben wir in unserer Familie zusätzlich einen Milchviehbetrieb den wir ebenfalls hervorheben möchten, da wir unseren Kunden gegenüber einerseits als Zulieferer aber auch als Kollege auftreten wollen.
Einzelfuttermittel: Hier können wir durch unsere Unabhängigkeit punkten, da wir nicht abhängig von bestimmten Lieferanten sind und dementsprechend unabhängig beraten können. Wir untersuchen im Vergleich zu unseren Wettbewerben die Qualität der Futtermittel bis ins Detail und können daher eine Transparenz bieten, die Konkurrenten in der Regel nicht bieten können. Unser Warenumschlagsplatz mit moderner Technik ermöglicht es uns äußerst kosteneffizient die Waren umschlagen und ausliefern zu können.
Mischfuttermittel: Auf Basis der vorhandenen Einzelfuttermittel stellen wir je nach Kundenwunsch individuelle Mischfutter her. Wir arbeiten mit offenen Deklarationen, sodass unsere Kunden jederzeit nachvollziehen können, ob auch die Einzelfuttermittel verwendet wurden, die sie bestellt haben und keine billigen Ersatzprodukte verwendet wurden.
Zudem sind wir BT und HUPA zertifiziert. Die aktuellen für unser Unternehmen ausgestellten Zertifikate müssen für unsere Kunden als Download zur Verfügung stehen. Statt dem HUPA-Logo bitte das ..
Aufgabenstellung
Wir möchten gerne ein zeitgemäße Homepage, jedoch muss auch berücksichtigt werden, dass unsere Kunden eher konservativ denken.

```html
<!DOCTYPE html>
<html lang="de">
<head>
<meta charset="utf-8">
<title>Auental Agrar – Produkte</title>
<link href="https://fonts.googleapis.com/css2?family=Inter:ital,wght@0,400;0,500;0,600;0,700;0,800;1,500&display=swap" rel="stylesheet">
<style>
:root{
  --green:#4a6a1c;
  --orange:#f5a90c;
  --yellow:#f4c920;
  --dark:#2a2a2a;
  --grey:#d9d9d9;
  --text:#1a1a1a;
  --white:#ffffff;
  --seal-a:#4e9e2f;
  --seal-b:#dbe7f3;
}
*{box-sizing:border-box;margin:0;padding:0}
html,body{width:1200px;height:3704px;overflow:hidden}
body{position:relative;background:var(--white);font-family:'Inter',sans-serif;color:var(--text)}
.abs{position:absolute}
/* header */
.site-header{left:0;top:0;width:1200px;height:115px;background:var(--green)}
.header-accent{left:0;top:0;width:69px;height:115px;background:var(--orange)}
.header-gap{left:69px;top:0;width:14px;height:115px;background:#e8e8e8}
.header-rule{left:0;top:115px;width:1200px;height:9px;background:#d6d6d6}
.brand{left:112px;top:36px;display:flex;align-items:center;gap:8px;color:var(--orange);font-weight:700;font-size:17px;line-height:1.1;width:110px}
.brand-dot{width:16px;height:16px;border-radius:50%;background:var(--orange);flex:none}
.nav{top:55px;font-size:13px;font-weight:700;color:var(--white);letter-spacing:.1px}
.nav.active{color:var(--orange)}
.search{left:1143px;top:50px}
.dropdown{left:829px;top:79px;width:134px;height:82px;background:var(--yellow)}
.dropdown div{font-size:8px;font-weight:800;padding:0 5px;height:20.5px;line-height:20.5px;border-bottom:1px solid #e0b400;white-space:nowrap;overflow:hidden}
.dropdown div:first-child{color:#fff}
/* products */
.h-products{left:0;width:1200px;top:220px;text-align:center;font-size:29px;font-weight:600}
.p-label{top:319px;font-size:11px;font-weight:700;text-align:center;width:220px}
.p-img{top:352px;height:188px}
.btn-more{top:527px;height:38px;border-radius:19px;background:var(--orange);color:#fff;font-weight:700;font-size:16px;display:flex;align-items:center;justify-content:center;width:126px}
/* yellow band */
.band{left:0;top:628px}
.feat{width:210px;text-align:center}
.feat h3{font-size:20px;font-weight:500;margin:8px 0 24px}
.feat p{font-size:17px;line-height:20px}
.feat svg{display:block;margin:0 auto}
.btn-lesen{left:852px;top:950px;width:198px;height:66px;border-radius:33px;background:var(--orange);font-size:20px;font-weight:600;display:flex;align-items:center;justify-content:center}
.badge-a{left:480px;top:1045px;width:86px;height:80px;background:var(--seal-a);border:3px solid #e6e6e6;border-radius:4px}
.badge-b{left:639px;top:1045px;width:71px;height:80px;background:var(--seal-b);border-radius:4px}
.und{left:585px;top:1068px;font-size:21px;font-weight:600}
.zert{left:480px;width:240px;top:1130px;text-align:center;font-size:28px;font-style:italic;font-weight:500}
.btn-dl{left:480px;top:1194px;width:240px;height:66px;border-radius:33px;background:var(--orange);font-size:19px;font-weight:600;display:flex;align-items:center;justify-content:center;text-align:center;line-height:22px}
.rule-y{left:0;top:1290px;width:1200px;height:5px;background:var(--yellow)}
/* detail */
.main-img{left:161px;top:1482px;width:392px;height:296px;background:linear-gradient(135deg,#8a5a2a,#d8a451 55%,#a36a2e)}
.thumb{top:1809px;width:132px;height:97px}
.arrow{top:1607px}
.d-title{left:655px;top:1413px;font-size:26px;font-weight:600}
.stat{left:655px;width:410px}
.stat span{display:block;font-size:19px;font-weight:600;margin-bottom:5px}
.bar{height:13px;border-radius:7px;background:var(--grey);overflow:hidden}
.bar i{display:block;height:100%;background:var(--yellow);border-radius:7px}
.d-sub{left:655px;top:1824px;font-size:23px;font-weight:600}
.btn-info{left:377px;top:1984px;width:451px;height:67px;border-radius:22px;background:var(--yellow);font-size:22px;font-weight:700;text-decoration:underline;display:flex;align-items:center;justify-content:center}
/* tabs */
.tab{top:2176px;font-size:23px;font-weight:500}
.tab-line{left:239px;top:2211px;width:171px;height:4px;background:var(--yellow)}
.panel{left:50px;top:2259px;width:1098px;height:386px;background:var(--yellow);border-radius:22px}
.row-l{left:91px;font-size:23px;font-weight:500}
.row-v{left:446px;font-size:20px;font-weight:500}
.bullet{left:436px;font-size:20px;font-weight:500}
/* similar */
.h-sim{left:68px;top:2736px;font-size:30px;font-weight:700}
.card{top:2851px;width:213px;height:320px}
.card .ph{height:211px}
.card .foot{height:109px;background:var(--yellow);position:relative}
.card h4{position:absolute;left:10px;top:19px;font-size:20px;font-weight:500}
.kaufen{position:absolute;left:10px;top:71px;background:#111;color:#fff;font-size:16px;font-weight:700;padding:4px 16px}
.heart{position:absolute;right:10px;top:75px}
/* footer */
.footer{left:0;top:3322px;width:1200px;height:330px;background:var(--dark)}
.copy-bar{left:0;top:3652px;width:1200px;height:52px;background:var(--yellow);font-size:11px;font-weight:600;text-align:center;line-height:52px}
.f-brand{left:126px;top:3420px;display:flex;align-items:center;gap:10px;color:var(--orange);font-size:28px;font-weight:700;line-height:1.1;width:200px}
.f-vline{top:3384px;width:2px;height:144px;background:#fff}
.f-vline::before,.f-vline::after{content:"";position:absolute;left:-3px;width:8px;height:8px;border-radius:50%;background:#fff}
.f-vline::before{top:-4px}.f-vline::after{bottom:-4px}
.nl-title{left:395px;top:3388px;color:#fff;font-size:20px;font-weight:600}
.nl-title b{font-size:25px}
.field{height:22px;background:#e0e0e0;font-size:9px;padding:4px 8px;color:#333}
.send{left:677px;top:3478px;width:128px;height:20px;background:var(--orange);font-size:10px;font-weight:800;text-align:center;line-height:20px}
.info{left:877px;color:#fff;font-size:11px;display:flex;align-items:center;gap:7px}
.kontakt{left:456px;top:3547px;font-size:20px;font-weight:700;color:var(--orange)}
.kontakt em{font-style:normal;color:#fff}
.wa{left:716px;top:3534px;width:52px;height:52px;border-radius:50%;background:#2fbf3d}
.soc{top:3611px;width:19px;height:19px;background:#fff;border-radius:4px}
</style>
</head>
<body>
<header>
  <div class="abs site-header"></div>
  <div class="abs header-accent"></div>
  <div class="abs header-gap"></div>
  <div class="abs header-rule"></div>
  <div class="abs brand"><span class="brand-dot"></span>Auental Agrar</div>
  <nav>
    <span class="abs nav active" style="left:484px">LANDWIRT</span>
    <span class="abs nav" style="left:572px">GESCHÄFTSPARTNER</span>
    <span class="abs nav" style="left:731px">LIEFERANTEN</span>
    <span class="abs nav" style="left:838px">PRODUKTE ▾</span>
    <span class="abs nav" style="left:940px">FIRMENPRÄSENTATION</span>
  </nav>
  <svg class="abs search" width="26" height="26" viewBox="0 0 26 26" fill="none" stroke="#fff" stroke-width="2.4"><circle cx="10" cy="10" r="7.5"/><path d="M15.5 15.5 24 24"/></svg>
  <div class="abs dropdown">
    <div>SOJAEXKTRAKTIONSSCHROT</div><div>MISCHFUTTERMITTEL</div><div>AGRARFOLIEN</div><div>SAATGUT</div>
  </div>
</header>

<section class="products">
  <h1 class="abs h-products">Produkte</h1>
  <div class="abs p-label" style="left:177px">SOJAEXKTRAKTIONSSCHROT</div>
  <div class="abs p-label" style="left:382px">MISCHFUTTERMITTEL</div>
  <div class="abs p-label" style="left:593px">AGRARFOLIEN</div>
  <div class="abs p-label" style="left:801px">SAATGUT</div>
  <div class="abs p-img" role="img" aria-label="Sojabohnen aus einem Jutesack auf Holz" style="left:193px;width:189px;background:linear-gradient(135deg,#8b5a2b,#d9a650 60%,#9c6530)"></div>
  <div class="abs p-img" role="img" aria-label="Mischfutter aus einem Metalleimer" style="left:401px;width:188px;background:linear-gradient(135deg,#5b4a3a,#8c6a4a 55%,#4a3b2e)"></div>
  <div class="abs p-img" role="img" aria-label="Strohballen unter Folie auf dem Feld" style="left:609px;width:188px;background:linear-gradient(180deg,#c9d4dc,#d9c7a0 40%,#b98a3a)"></div>
  <div class="abs p-img" role="img" aria-label="Haufen Saatgutkörner" style="left:839px;width:152px;background:radial-gradient(circle,#b98a55 0%,#c9a070 55%,#ffffff 72%)"></div>
  <div class="abs btn-more" style="left:224px">mehr sehen</div>
  <div class="abs btn-more" style="left:433px">mehr sehen</div>
  <div class="abs btn-more" style="left:650px">mehr sehen</div>
  <div class="abs btn-more" style="left:855px">mehr sehen</div>
</section>

<section>
  <svg class="abs band" width="1200" height="464" viewBox="0 0 1200 464"><polygon points="0,0 1200,0 1200,464 0,308" fill="#f4c920"/></svg>
  <div class="abs feat" style="left:167px;top:650px">
    <svg width="44" height="44" viewBox="0 0 44 44"><path d="M22 3 40 9v12c0 11-8 18-18 21C12 39 4 32 4 21V9z" fill="#111"/><path d="M22 30c0-6 4-10 9-10-1 6-4 9-9 10zm0 0c0-6-4-10-9-10 1 6 4 9 9 10z" fill="#f4c920"/></svg>
    <h3>Lorem Ipsum</h3>
    <p>Excepteur sint occaecat cupidatat non proident, sunt in Excepteur sint occaecat cupidatat non Excepteur sint occaecat cupidatat non proident, sunt in culpa , sunt in culpa</p>
  </div>
  <div class="abs feat" style="left:385px;top:648px">
    <svg width="44" height="50" viewBox="0 0 44 50"><path d="M12 30 6 48l8-4 4 6 4-14zm20 0 6 18-8-4-4 6-4-14z" fill="#111"/><circle cx="22" cy="18" r="16" fill="#111"/><circle cx="22" cy="18" r="10" fill="none" stroke="#f4c920" stroke-width="2"/><path d="m16 18 4 4 8-8" fill="none" stroke="#f4c920" stroke-width="3"/></svg>
    <h3>Lorem Ipsum</h3>
    <p>Excepteur sint occaecat cupidatat non proident, sunt in Excepteur sint occaecat cupidatat non Excepteur sint occaecat cupidatat non proident, sunt in culpa , sunt in culpa</p>
  </div>
  <div class="abs feat" style="left:606px;top:652px">
    <svg width="42" height="42" viewBox="0 0 42 42"><circle cx="21" cy="21" r="20" fill="#111"/><path d="M21 30c0-7 5-12 11-12-1 7-5 11-11 12zm0 0c0-7-5-12-11-12 1 7 5 11 11 12z" fill="#f4c920"/></svg>
    <h3>Lorem Ipsum</h3>
    <p>Excepteur sint occaecat cupidatat non proident, sunt in Excepteur sint occaecat cupidatat non Excepteur sint occaecat cupidatat non proident, sunt in culpa , sunt in culpa</p>
  </div>
  <div class="abs feat" style="left:822px;top:646px">
    <svg width="50" height="50" viewBox="0 0 50 50"><path d="M18 4h14v8l-7 5-7-5z" fill="none" stroke="#111" stroke-width="2"/><path d="m21 8 3 3 5-5" fill="none" stroke="#111" stroke-width="2"/><path d="M2 26 12 20l12 8 4-3 20 3-8 12-10 4-14-6-14-2z" fill="#111"/></svg>
    <h3>Lorem Ipsum</h3>
    <p>Excepteur sint occaecat cupidatat non proident, sunt in Excepteur sint occaecat cupidatat non Excepteur sint occaecat cupidatat non proident, sunt in culpa , sunt in culpa</p>
  </div>
  <div class="abs btn-lesen">mehr lesen</div>

  <div class="abs badge-a" role="img" aria-label="HUPA Prüfsiegel"></div>
  <div class="abs und">und</div>
  <div class="abs badge-b" role="img" aria-label="BT Zertifizierungssiegel"></div>
  <div class="abs zert">zertifiziert</div>
  <div class="abs btn-dl">herunterladen<br>zertifikat</div>
  <div class="abs rule-y"></div>
</section>

<section class="detail">
  <svg class="abs" style="left:518px;top:1422px" width="36" height="36" viewBox="0 0 36 36" fill="none" stroke="#111" stroke-width="4"><circle cx="13" cy="13" r="9"/><path d="m20 20 12 12"/></svg>
  <div class="abs main-img" role="img" aria-label="Sojabohnen aus einem Jutesack mit Holzlöffel"></div>
  <div class="abs thumb" role="img" aria-label="Sojabohnen im Sack" style="left:161px;background:linear-gradient(135deg,#c9b596,#d4a452 60%,#8c6a40)"></div>
  <div class="abs thumb" role="img" aria-label="Sojabohnen in einer Holzschaufel" style="left:313px;background:linear-gradient(135deg,#6e5436,#c79a58 55%,#5a442c)"></div>
  <svg class="abs arrow" style="left:32px" width="58" height="46" viewBox="0 0 58 46"><polygon points="0,23 58,0 58,46" fill="#f5a90c"/></svg>
  <svg class="abs arrow" style="left:1121px" width="58" height="46" viewBox="0 0 58 46"><polygon points="58,23 0,0 0,46" fill="#f5a90c"/></svg>

  <h2 class="abs d-title">Sojaexktraktionsschrot</h2>
  <div class="abs stat" style="top:1474px"><span>Feuchtigkeitsgehalt - 10,6%</span><div class="bar"><i style="width:27%"></i></div></div>
  <div class="abs stat" style="top:1528px"><span>Rohprotein - 32,8%</span><div class="bar"><i style="width:55%"></i></div></div>
  <div class="abs stat" style="top:1582px"><span>Rohfett - 3,3%</span><div class="bar"><i style="width:11%"></i></div></div>
  <div class="abs stat" style="top:1636px"><span>Rohfaser - 12,2%</span><div class="bar"><i style="width:27%"></i></div></div>
  <div class="abs stat" style="top:1690px"><span>Stärke - 5,0%</span><div class="bar"><i style="width:15%"></i></div></div>
  <div class="abs stat" style="top:1744px"><span>Zucker - 10,5%</span><div class="bar"><i style="width:27%"></i></div></div>
  <h3 class="abs d-sub">Besonderheiten</h3>
  <div class="abs stat" style="top:1864px"><span>Pansenstabilität (Eiweiß) - 75,0%</span><div class="bar"><i style="width:82%"></i></div></div>

  <div class="abs btn-info">Weitere Informationen Anfordern</div>
</section>

<section class="tabs">
  <div class="abs tab" style="left:247px">Beschreibung</div>
  <div class="abs tab" style="left:461px">Zusatzliche Informationen</div>
  <div class="abs tab" style="left:806px">Ein Muster Anfragen</div>
  <div class="abs tab-line"></div>
  <div class="abs panel"></div>
  <div class="abs row-l" style="top:2290px">Zusammensetzung</div>
  <div class="abs row-l" style="top:2334px">Einsatzempfehlung</div>
  <div class="abs row-l" style="top:2378px">Haltbarkeit</div>
  <div class="abs row-l" style="top:2422px">Vorteile</div>
  <div class="abs row-v" style="top:2292px">Rapsschrot</div>
  <div class="abs row-v" style="top:2336px">Milchkühe: Bis Zu 3 Kg Pro Tier Pro Tag, Abhängig Von Der Ration</div>
  <div class="abs row-v" style="top:2380px;left:449px">Mehrere Monate Bei Trockener Lagerung</div>
  <div class="abs bullet" style="top:2424px">• Das Futterprotein Wird Effizient Genutzt</div>
  <div class="abs bullet" style="top:2461px">• Gute Futteraufnahme Durch Gute Schmackhaftigkeit</div>
  <div class="abs bullet" style="top:2498px">• Hoher Pansenschutz Der Proteine</div>
  <div class="abs bullet" style="top:2536px">• Hohe Dünndarmverdaulichkeit</div>
  <div class="abs bullet" style="top:2573px">• Geringere Umweltbelastung Durch Reduzierte Stickstoffausscheidung</div>
</section>

<section class="similar">
  <h2 class="abs h-sim">Ähnliche Produkte</h2>
  <div class="abs card" style="left:50px">
    <div class="ph" role="img" aria-label="Haufen Saatgutkörner" style="background:radial-gradient(circle,#b98a55 0%,#c9a070 50%,#ffffff 70%)"></div>
    <div class="foot"><h4>Lorem Ipsum</h4><span class="kaufen">Kaufen</span><svg class="heart" width="22" height="20" viewBox="0 0 22 20"><path d="M11 19 2 10C-1 6 2 1 6 1c2 0 4 1 5 3 1-2 3-3 5-3 4 0 7 5 4 9z" fill="#e3262b"/></svg></div>
  </div>
  <div class="abs card" style="left:345px">
    <div class="ph" role="img" aria-label="Mischfutter aus einem Metalleimer" style="background:linear-gradient(135deg,#5b4a3a,#8c6a4a 55%,#4a3b2e)"></div>
    <div class="foot"><h4>Lorem Ipsum</h4><span class="kaufen">Kaufen</span><svg class="heart" width="22" height="20" viewBox="0 0 22 20"><path d="M11 19 2 10C-1 6 2 1 6 1c2 0 4 1 5 3 1-2 3-3 5-3 4 0 7 5 4 9z" fill="#e3262b"/></svg></div>
  </div>
  <div class="abs card" style="left:639px">
    <div class="ph" role="img" aria-label="Sojabohnen aus einem Jutesack" style="background:linear-gradient(135deg,#8b5a2b,#d9a650 60%,#9c6530)"></div>
    <div class="foot"><h4>Lorem Ipsum</h4><span class="kaufen">Kaufen</span><svg class="heart" width="22" height="20" viewBox="0 0 22 20"><path d="M11 19 2 10C-1 6 2 1 6 1c2 0 4 1 5 3 1-2 3-3 5-3 4 0 7 5 4 9z" fill="#e3262b"/></svg></div>
  </div>
  <div class="abs card" style="left:935px">
    <div class="ph" role="img" aria-label="Strohballen unter Folie auf dem Feld" style="background:linear-gradient(180deg,#c9d4dc,#d9c7a0 35%,#b98a3a)"></div>
    <div class="foot"><h4>Lorem Ipsum</h4><span class="kaufen">Kaufen</span><svg class="heart" width="22" height="20" viewBox="0 0 22 20"><path d="M11 19 2 10C-1 6 2 1 6 1c2 0 4 1 5 3 1-2 3-3 5-3 4 0 7 5 4 9z" fill="#e3262b"/></svg></div>
  </div>
</section>

<footer>
  <div class="abs footer"></div>
  <div class="abs f-brand"><span class="brand-dot" style="width:22px;height:22px"></span>Auental Agrar</div>
  <div class="abs f-vline" style="left:355px"></div>
  <div class="abs f-vline" style="left:842px"></div>
  <div class="abs nl-title">Abonnieren Sie Unseren <b>Newsletter</b></div>
  <div class="abs field" style="left:395px;top:3427px;width:127px">Name</div>
  <div class="abs field" style="left:536px;top:3427px;width:126px">Email</div>
  <div class="abs field" style="left:677px;top:3427px;width:128px">Telefonnummer</div>
  <div class="abs field" style="left:395px;top:3467px;width:267px;height:31px">Nachricht</div>
  <div class="abs send">SCHICKEN</div>
  <div class="abs info" style="top:3436px"><svg width="9" height="12" viewBox="0 0 9 12"><path d="M4.5 12S0 7 0 4.5a4.5 4.5 0 0 1 9 0C9 7 4.5 12 4.5 12z" fill="#fff"/><circle cx="4.5" cy="4.5" r="1.6" fill="#2a2a2a"/></svg>Locatins</div>
  <div class="abs info" style="top:3455px"><svg width="10" height="10" viewBox="0 0 10 10"><circle cx="5" cy="5" r="5" fill="#fff"/><path d="M3 2.5 4 4 3.5 5c.4.8 1 1.4 1.8 1.8L6 6.2l1.5 1L7 8C5 8 2 5 2 3z" fill="#2a2a2a"/></svg>+49 0000 123456</div>
  <div class="abs info" style="top:3474px"><svg width="10" height="8" viewBox="0 0 10 8"><rect width="10" height="8" fill="#fff"/><path d="m0 0 5 4 5-4" fill="none" stroke="#2a2a2a"/></svg>info@auental-agrar.example</div>
  <div class="abs kontakt">Kontaktieren Sie Uns <em>per</em></div>
  <div class="abs wa" role="img" aria-label="Messenger-Kontakt"></div>
  <div class="abs soc" style="left:555px"></div>
  <div class="abs soc" style="left:578px"></div>
  <div class="abs soc" style="left:601px"></div>
  <div class="abs soc" style="left:624px"></div>
  <div class="abs copy-bar">Copyright 2023 All Right Reserved</div>
</footer>
</body>
</html>
```